Doctor Formulated Medical Cosmetics

Velour Skinhaus is an E-commerce site for high end Medical Cosmetics designed to treat specific skin problems. The Velour Skinhaus difference/advantage is that all creams and serums are:
Doctor Formulated, Freshly Handmade, Registered Pharmacy.
The Site also provides real doctor Dermatology Consultations, Library (with a list of - 1. Active Ingredients in the creams with description of their effects, 2. Skin Conditions with information on what causes the condition and typical treatment approaches and outcomes. 3. Resources from Dermatology Journals and literature on the conditions.)
Header Information: Velour Skinhaus, languages EN, BG, Register / log in, Shopping Bag. This field should be narrow.
Categories (horizontal): Home, Face, Body, Hair Care, Skin Conditions, Doctor Consultation, Library
The Landing Page should have only one well organized picture, which is intended to create the feeling of luxury, freedom and relaxation. It will be large and will fill the whole screen. All text should be on transparent or similar color fields. Please use the color of the text to create also the feeling of conservative luxury.
Written message / image overlay Velour Skinhaus(logo), Skin Care, Doctor Formulated, Freshly Handmade, Registered Pharmacy.
Please study the Landing Page of this site as an example: www.marivane.com
Under the Landing Page, there should be a slider with 4 of our products.
Underneath: Four Blog Articles (large pictures for maximum impact and luxury text underneath).
Underneath: Banner for Dermatologist Consultation, (button for Start Your Case Now).
Underneath: Two pictures in a line - Library (with books), and Active Ingredients.
Footer: Philosophy, Categories, Customer Care
Please adhere to the color palate provided in the pictures (as attachments). Provided are some examples of Web Sites with the desired look and feel. www.quillora.com , www.tavenholtmd.com .
Please use different shades of gray, white, beige and gold colors, and black. Our products will be in brown glass jars and bottles to convey the professional, pharmacy made nature of the creams and lotions.
We find the following Front Page very attractive and effective - www.marivane.com , with its full page image and overlaying text.
Please have a look at this link for the Landing page.
http://www.brimlensphoto.com/detail/video/woman-lying-on-a-black-sand-beach-in-a-bikini-stock-footage/58213067
I would like to use it in the animated version to achieve the WOW effect. I have uploaded the jpeg version for it, so you will be able create your design.
For the Landing page design, please use only the two uploaded pictures of a woman laying at the beach. Let's see how each of them will look like.
Thank you for your help.

```html
<!DOCTYPE html>
<html lang="en">
<head>
<meta charset="utf-8">
<title>Velour Skinhaus — Doctor Formulated Medical Cosmetics</title>
<link rel="stylesheet" href="https://fonts.googleapis.com/css2?family=Roboto+Slab:wght@300;400;500&family=Open+Sans:wght@400;600;700&display=swap">
<style>
:root{
  --gold:#c9a45a;
  --gold-light:#dcbd78;
  --gold-dark:#a9823c;
  --gold-band:#d5b26b;
  --ink:#1e1e1e;
  --charcoal:#2b2926;
  --line:#dcdcdc;
  --white:#ffffff;
  --text:#3a3a3a;
}
*{box-sizing:border-box;margin:0;padding:0}
html,body{width:1200px;height:3237px;overflow:hidden}
body{font-family:"Open Sans",Arial,sans-serif;color:var(--text);background:var(--white);position:relative}
.abs{position:absolute}

/* brand lockup: name + one plain circle */
.brand{display:flex;align-items:center;gap:14px;color:var(--gold);font-family:"Roboto Slab",Georgia,serif;font-weight:300;white-space:nowrap}
.brand-dot{flex:none;border-radius:50%;background:radial-gradient(circle at 35% 30%,var(--gold-light),var(--gold) 60%,var(--gold-dark))}

/* header */
.site-header{left:0;top:0;width:1200px;height:121px;background:var(--white);border-top:3px solid var(--ink)}
.site-header .brand{left:97px;top:30px;font-size:36px}
.site-header .brand-dot{width:58px;height:58px}
.lang{left:505px;top:40px;width:96px;height:34px;border:1px solid #bbb;border-radius:3px;display:flex;align-items:center;gap:6px;padding:0 6px;font-size:13px;color:#333}
.lang .flag{width:32px;height:22px;background:linear-gradient(#23397a,#c8102e 50%,#23397a)}
.top-links{left:617px;top:46px;font-size:16px;color:#222;word-spacing:10px}
.bag{left:813px;top:40px}
.btn-register,.btn-login{top:39px;height:42px;width:103px;border-radius:3px;display:flex;align-items:center;justify-content:center;font-size:14px;color:#fff;font-weight:600}
.btn-register{left:883px;background:var(--gold)}
.btn-login{left:997px;background:var(--ink)}

/* nav */
.main-nav{left:0;top:121px;width:1200px;height:62px;background:linear-gradient(var(--gold-light),var(--gold-dark));display:flex;align-items:center;padding-left:97px}
.main-nav a{color:#fff;text-decoration:none;font-size:15px;font-weight:600;padding:0 14px;height:62px;display:flex;align-items:center}
.main-nav a.active{background:var(--charcoal)}

/* hero */
.hero{left:0;top:183px;width:1200px;height:497px;background:linear-gradient(90deg,#ececec,#dedede);overflow:hidden}
.hero-photo{right:0;top:0;width:700px;height:497px;background:
  radial-gradient(ellipse 55% 70% at 68% 45%,#e9c3a8 0%,#d39a78 35%,rgba(160,95,60,.85) 62%,rgba(222,222,222,0) 100%),
  linear-gradient(90deg,rgba(222,222,222,1) 0%,rgba(222,222,222,0) 30%,#b87a55 70%,#e4d6cb 100%)}
.hero .brand{left:97px;top:65px;font-size:40px;line-height:1.05}
.hero .brand-dot{width:112px;height:112px}
.hero-text{left:97px;top:210px;font-family:"Roboto Slab",Georgia,serif;font-size:26px;line-height:43px;color:#222;width:460px}
.dots{left:97px;top:373px;display:flex;gap:6px}
.dots span{width:17px;height:17px;border:2px solid #555;border-radius:50%}
.dots span.on{background:var(--gold);border-color:var(--gold-dark)}

/* section title */
.section-title{left:0;width:1200px;display:flex;justify-content:center;align-items:center;gap:14px;font-family:"Roboto Slab",Georgia,serif;font-size:33px;color:var(--gold)}
.section-title .word{border-top:2px solid currentColor;border-bottom:2px solid currentColor;padding:6px 4px;line-height:1.2}
.section-title .dot{width:56px;height:56px;border-radius:50%;background:radial-gradient(circle at 35% 30%,var(--gold-light),var(--gold) 60%,var(--gold-dark))}
.section-title.light{color:#fff}
.section-title.light .dot{background:radial-gradient(circle at 35% 30%,#fff,#f3e6c8)}

/* products */
.product-card{top:816px;width:236px;height:302px;border:1px solid var(--line);border-radius:4px;background:#fff;box-shadow:0 1px 4px rgba(0,0,0,.08)}
.product-photo{position:absolute;left:30px;top:14px;width:176px;height:150px;background:radial-gradient(ellipse 60% 55% at 50% 60%,var(--tone) 0%,rgba(255,255,255,0) 75%),#fff}
.product-name{position:absolute;top:180px;width:100%;text-align:center;font-size:17px;color:#222}
.product-desc{position:absolute;top:214px;width:100%;text-align:center;font-size:13px;color:#444}
.price{position:absolute;left:30px;top:252px;font-size:15px;color:#222}
.cart{position:absolute;right:14px;top:242px;width:102px;height:36px;border-radius:3px;background:#444;color:#fff;font-size:13px;display:flex;align-items:center;justify-content:center}
.cart.gold{background:var(--gold)}

/* blog */
.blog{left:0;top:1161px;width:1200px;height:766px;background:var(--gold-band)}
.blog-tile{width:583px;height:286px;box-shadow:0 2px 6px rgba(0,0,0,.25)}
.blog-tile h3{position:absolute;left:22px;bottom:48px;color:#fff;font-size:19px;font-weight:700}
.blog-tile p{position:absolute;left:22px;bottom:24px;color:#f1f1f1;font-size:14px}

/* consultation */
.consult{left:0;top:1927px;width:1200px;height:393px;background:linear-gradient(120deg,#f2f2f2,#e4e4e4);overflow:hidden}
.consult-photo{right:0;top:0;width:420px;height:393px;background:
  radial-gradient(ellipse 55% 65% at 60% 50%,#e8bfa6 0%,#c98b6c 40%,rgba(138,90,69,.8) 65%,rgba(230,230,230,0) 100%),
  linear-gradient(90deg,rgba(228,228,228,1) 0%,rgba(228,228,228,0) 25%,#9c6a52 70%,#efe9e3 100%)}
.consult .brand{left:210px;top:62px;font-size:40px}
.consult .brand-dot{width:64px;height:64px}
.consult h2{left:0;top:157px;width:734px;text-align:center;font-family:"Roboto Slab",Georgia,serif;font-size:33px;color:var(--gold-dark);font-weight:500}
.consult p{left:90px;top:221px;width:554px;text-align:center;font-size:13px;line-height:27px;color:#555}
.btn-dark{left:302px;top:298px;width:130px;height:45px;background:var(--ink);color:#fff;font-size:15px;font-weight:600;display:flex;align-items:center;justify-content:center}

/* articles */
.article-card{top:2449px;width:236px;height:350px;background:#fff;box-shadow:0 1px 4px rgba(0,0,0,.18);border-bottom:3px solid #444}
.article-card.active{border-bottom-color:var(--gold)}
.article-photo{height:164px}
.article-card h4{position:absolute;top:180px;width:100%;text-align:center;font-family:"Roboto Slab",Georgia,serif;font-size:15px;font-weight:500;color:#222}
.article-card.active h4{color:var(--gold-dark)}
.article-card p{position:absolute;left:16px;top:210px;width:204px;text-align:center;font-size:11.5px;line-height:21px;color:#444}
.btn-outline{position:absolute;left:72px;top:292px;width:92px;height:36px;border:1px solid #333;border-radius:3px;font-size:13px;color:#222;display:flex;align-items:center;justify-content:center}
.article-card.active .btn-outline{background:var(--gold);border-color:var(--gold);color:#fff}

/* footer */
.site-footer{left:0;top:2840px;width:1200px;height:337px;background:var(--charcoal)}
.site-footer .brand{left:97px;top:100px;font-size:27px;color:#fff;gap:10px}
.site-footer .brand-dot{width:50px;height:50px}
.social{left:128px;top:198px;display:flex;gap:8px}
.social span{width:34px;height:34px;border:2px solid #fff;border-radius:50%}
.footer-title{top:52px;color:#fff;font-size:17px;font-weight:700;letter-spacing:.5px}
.quick-links{left:384px;top:92px;list-style:none;color:#fff;font-size:14px;line-height:32px}
.contact-row{left:561px;display:flex;gap:16px;color:#fff;font-size:13px;line-height:20px}
.contact-row .ic{width:38px;height:38px;border:2px solid #fff;border-radius:50%;flex:none;display:flex;align-items:center;justify-content:center}
.field{border:1px solid #ccc;border-radius:3px;color:#eee;font-size:11px;padding:8px 10px}
.btn-send{left:814px;top:220px;width:118px;height:37px;background:var(--gold);border:1px solid #fff;color:#fff;font-size:12px;display:flex;align-items:center;justify-content:center}
.bottom-bar{left:0;top:3177px;width:1200px;height:60px;background:linear-gradient(var(--gold-light),var(--gold-dark));color:#fff;font-size:14px;display:flex;align-items:center;justify-content:center}
</style>
</head>
<body>

<header class="site-header abs">
  <div class="brand abs"><span class="brand-dot"></span><span>Velour Skinhaus</span></div>
  <div class="lang abs"><span class="flag"></span>Eng ▾</div>
  <div class="top-links abs">Doctor | Pharmacy</div>
  <svg class="bag abs" width="38" height="40" viewBox="0 0 38 40" aria-hidden="true"><path d="M11 14v-4a8 8 0 0 1 16 0v4" fill="none" stroke="#b8913f" stroke-width="3"/><rect x="3" y="14" width="32" height="24" rx="2" fill="#c9a45a"/></svg>
  <div class="btn-register abs">REGISTER</div>
  <div class="btn-login abs">LOGIN</div>
</header>

<nav class="main-nav abs">
  <a class="active">HOME</a><a>FACE</a><a>BODY</a><a>HAIR CARE</a><a>SKIN CONCERNS</a><a>DERMATOLOGIST CONSULTATION</a><a>LIBRARY</a><a>CONTACT US</a>
</nav>

<section class="hero abs">
  <div class="hero-photo abs" role="img" aria-label="Portrait photograph of a smiling woman with long auburn hair"></div>
  <div class="brand abs"><span class="brand-dot"></span><span>Velour<br>Skinhaus</span></div>
  <p class="hero-text abs">Doctor Formulated, Freshly Hand made, Registered Pharmacy, Highest Ethical Standards</p>
  <div class="dots abs"><span class="on"></span><span></span><span></span><span></span><span></span></div>
</section>

<div class="section-title abs" style="top:712px"><span class="word">Velour Skinhaus</span><span class="dot"></span><span class="word">Products</span></div>

<div class="product-card abs" style="left:97px"><div class="product-photo" style="--tone:#e4e4e6" role="img" aria-label="White cosmetic bottles and jars"></div><div class="product-name">Product Name</div><div class="product-desc">Nemo enim ipsam voluptatem</div><div class="price">$55.50</div><div class="cart gold">Add to Cart</div></div>
<div class="product-card abs" style="left:354px"><div class="product-photo" style="--tone:#bfe0dc" role="img" aria-label="Teal and white serum bottles"></div><div class="product-name">Product Name</div><div class="product-desc">Nemo enim ipsam voluptatem</div><div class="price">$55.50</div><div class="cart">Add to Cart</div></div>
<div class="product-card abs" style="left:611px"><div class="product-photo" style="--tone:#f0d68a" role="img" aria-label="Gold cosmetic tubes and dropper bottle"></div><div class="product-name">Product Name</div><div class="product-desc">Nemo enim ipsam voluptatem</div><div class="price">$55.50</div><div class="cart">Add to Cart</div></div>
<div class="product-card abs" style="left:865px"><div class="product-photo" style="--tone:#cfdcc0" role="img" aria-label="Green and white cream jars"></div><div class="product-name">Product Name</div><div class="product-desc">Nemo enim ipsam voluptatem</div><div class="price">$55.50</div><div class="cart">Add to Cart</div></div>

<section class="blog abs">
  <div class="section-title light abs" style="top:30px"><span class="word">Our Blog</span><span class="dot"></span><span class="word">Articles</span></div>
  <div class="blog-tile abs" style="left:11px;top:136px;background:linear-gradient(rgba(0,0,0,0) 50%,rgba(0,0,0,.55)),radial-gradient(ellipse at 55% 40%,#b08a68,#5a4332 60%,#2e241c)" role="img" aria-label="Photograph of a woman with windswept hair"><h3>Nemo enim ipsam voluptatem</h3><p>Sed ut perspiciatis unde omnis</p></div>
  <div class="blog-tile abs" style="left:606px;top:136px;background:linear-gradient(rgba(0,0,0,0) 50%,rgba(0,0,0,.5)),radial-gradient(ellipse at 55% 40%,#d8cfc0,#7d8388 60%,#454b50)" role="img" aria-label="Photograph of a blonde woman against a grey wall"><h3>Nemo enim ipsam voluptatem</h3><p>Sed ut perspiciatis unde omnis</p></div>
  <div class="blog-tile abs" style="left:11px;top:438px;background:linear-gradient(rgba(0,0,0,0) 50%,rgba(0,0,0,.55)),radial-gradient(ellipse at 50% 45%,#8a8088,#4a4450 60%,#2e2a34)" role="img" aria-label="Photograph of a couple sitting by a city fountain"><h3>Nemo enim ipsam voluptatem</h3><p>Sed ut perspiciatis unde omnis</p></div>
  <div class="blog-tile abs" style="left:606px;top:438px;background:linear-gradient(rgba(0,0,0,0) 50%,rgba(0,0,0,.45)),radial-gradient(ellipse at 65% 45%,#c8a878,#5f9480 55%,#2a5a4e)" role="img" aria-label="Photograph of a woman in sunglasses by a green fence"><h3>Nemo enim ipsam voluptatem</h3><p>Sed ut perspiciatis unde omnis</p></div>
</section>

<section class="consult abs">
  <div class="consult-photo abs" role="img" aria-label="Portrait photograph of a woman with eyes closed and glamorous makeup"></div>
  <div class="brand abs"><span class="brand-dot"></span><span>Velour Skinhaus</span></div>
  <h2 class="abs">Dermatologist Consultation</h2>
  <p class="abs">Nemo enim ipsam voluptatem quia voluptas sit aspernatur aut odit aut fugit, sed quia consequuntur magni dolores eos qui ratione voluptatem</p>
  <div class="btn-dark abs">READ MORE</div>
</section>

<div class="section-title abs" style="top:2355px"><span class="word">Velour Skinhaus</span><span class="dot"></span><span class="word">Articles</span></div>

<article class="article-card abs" style="left:97px"><div class="article-photo" style="background:radial-gradient(ellipse at 50% 40%,#d9c6ae,#9a846c 60%,#5e4c3c)" role="img" aria-label="Photograph of a woman in a knit scarf"></div><h4>NEMO ENIM IPSAM</h4><p>Nemo enim ipsam voluptatem quia voluptas sit aspernatur aut odit aut fugit, sed quia consequuntur.</p><div class="btn-outline">Read More</div></article>
<article class="article-card active abs" style="left:354px"><div class="article-photo" style="background:radial-gradient(ellipse at 50% 40%,#f0dcb8,#c29a68 55%,#6e5034)" role="img" aria-label="Photograph of a blonde woman with long hair"></div><h4>NEMO ENIM IPSAM</h4><p>Nemo enim ipsam voluptatem quia voluptas sit aspernatur aut odit aut fugit, sed quia consequuntur.</p><div class="btn-outline">Read More</div></article>
<article class="article-card abs" style="left:611px"><div class="article-photo" style="background:radial-gradient(ellipse at 55% 55%,#4a9ccc,#24507a 55%,#121c2a)" role="img" aria-label="Photograph of a woman in a blue dress at night"></div><h4>NEMO ENIM IPSAM</h4><p>Nemo enim ipsam voluptatem quia voluptas sit aspernatur aut odit aut fugit, sed quia consequuntur.</p><div class="btn-outline">Read More</div></article>
<article class="article-card abs" style="left:865px"><div class="article-photo" style="background:radial-gradient(ellipse at 55% 50%,#e8c2a0,#e2a6bc 55%,#c88aa4)" role="img" aria-label="Photograph of a woman among pink blossoms"></div><h4>NEMO ENIM IPSAM</h4><p>Nemo enim ipsam voluptatem quia voluptas sit aspernatur aut odit aut fugit, sed quia consequuntur.</p><div class="btn-outline">Read More</div></article>

<footer class="site-footer abs">
  <div class="brand abs"><span class="brand-dot"></span><span>Velour Skinhaus</span></div>
  <div class="social abs"><span></span><span></span><span></span><span></span><span></span></div>

  <div class="footer-title abs" style="left:384px">QUICK LINKS</div>
  <ul class="quick-links abs"><li>› Home</li><li>› Team</li><li>› Programs</li><li>› Blog</li><li>› Our Story</li><li>› Contact Us</li></ul>

  <div class="footer-title abs" style="left:561px">CONTACT US</div>
  <div class="contact-row abs" style="top:100px"><span class="ic"><svg width="14" height="18" viewBox="0 0 14 18"><path d="M7 1a6 6 0 0 0-6 6c0 4 6 10 6 10s6-6 6-10a6 6 0 0 0-6-6z" fill="#fff"/><circle cx="7" cy="7" r="2" fill="#2b2926"/></svg></span><div><b>VELOUR SKINHAUS,</b><br>412 Harlow Crescent, Suite 12<br>Eastbrook ON K4T 7P2</div></div>
  <div class="contact-row abs" style="top:172px"><span class="ic"><svg width="12" height="18" viewBox="0 0 12 18"><rect x="1" y="1" width="10" height="16" rx="2" fill="none" stroke="#fff" stroke-width="2"/></svg></span><div><b>PHONE:</b><br>1800 4417 2290</div></div>
  <div class="contact-row abs" style="top:232px"><span class="ic"><svg width="18" height="12" viewBox="0 0 18 12"><rect x="0" y="0" width="18" height="12" rx="1" fill="#fff"/><path d="M0 0l9 7 9-7" fill="none" stroke="#2b2926" stroke-width="1.5"/></svg></span><div><b>Mail:</b><br>hello@velourskinhaus.example</div></div>

  <div class="footer-title abs" style="left:814px">CONTACT FORM</div>
  <div class="field abs" style="left:814px;top:95px;width:138px;height:36px">Name</div>
  <div class="field abs" style="left:962px;top:95px;width:138px;height:36px">Phone</div>
  <div class="field abs" style="left:814px;top:138px;width:286px;height:65px">Message</div>
  <div class="btn-send abs">SEND MESSAGE</div>
</footer>

<div class="bottom-bar abs">Copyright © 2016 Velour Skinhaus. All Right Reserved</div>

</body>
</html>
```